Stationary design for boutique production house

We need a stationary design for our production house, 'Lorno Productions' based in Singapore. We produce microfilms as well as podcasts, talkshows and events. Our logo is a stylized icon of our director, who is also the executive producer and host of our programs, Lorno. Our main company colors are Red, Black and white. We would like a clean, minimalist design incorporating our existing company logo that conveys a sense of urbanism and elegance.

Logo and font files are attached. f

Target Market(s)

We focus on lifestyle media rather than entertainment.

Industry/Entity Type

Boutique

Font styles to use
Serif
Sans Serif

Colors
ec1f27
ffffff
000000

Requirements
Must have
• Our company logo and at least one of our company colors.
Nice to have
• Our address and contact information.
Should not have
• Changes made to the company logo (using only certain parts of it is fine though)

```html
<!DOCTYPE html>
<html lang="en">
<head>
<meta charset="utf-8">
<title>Lorno Productions – Business Card</title>
<link rel="stylesheet" href="https://fonts.googleapis.com/css2?family=Source+Serif+4:wght@400;600;700&display=swap">
<style>
  :root {
    --brand-red: #ce161d;
    --brand-black: #1e1c1d;
    --paper-white: #f7f7f7;
    --text-white: #ffffff;
    --backdrop: #4d4d4d;
  }
  * { box-sizing: border-box; margin: 0; padding: 0; }
  html, body { width: 1200px; height: 750px; overflow: hidden; }
  body {
    background: var(--backdrop);
    font-family: "Source Serif 4", Georgia, serif;
    position: relative;
  }
  .card {
    position: absolute;
    top: 228px;
    width: 461px;
    height: 262px;
    overflow: hidden;
  }
  .card--front { left: 124px; background: var(--brand-red); color: var(--text-white); }
  .card--back { left: 595px; background: var(--paper-white); }

  .holder { position: absolute; left: 37px; top: 38px; }
  .holder__name { font-size: 17px; font-weight: 700; letter-spacing: 0.3px; line-height: 20px; }
  .holder__title { font-size: 13px; margin-top: 2px; }
  .address { position: absolute; left: 37px; top: 95px; font-size: 11.5px; line-height: 16px; }
  .contacts { position: absolute; left: 37px; top: 134px; list-style: none; font-size: 11.5px; }
  .contacts li { display: flex; align-items: center; height: 18.5px; white-space: nowrap; }
  .contacts svg { width: 12px; height: 12px; margin-right: 9px; fill: var(--text-white); }

  .front-mark {
    position: absolute; right: 34px; top: 70px;
    display: flex; flex-direction: column; align-items: flex-end; gap: 10px;
    font-weight: 600; text-transform: uppercase; text-align: right;
  }
  .front-mark__dot { width: 30px; height: 30px; border-radius: 50%; background: var(--text-white); }
  .front-mark__name { font-size: 26px; line-height: 30px; letter-spacing: 2px; }

  .wordmark {
    position: absolute; left: 301px; top: 62px; transform: translateX(-50%);
    display: flex; flex-direction: column; align-items: center; gap: 12px;
    font-weight: 600; color: var(--brand-black);
    text-transform: uppercase; text-align: center; white-space: nowrap;
  }
  .wordmark__dot { width: 30px; height: 30px; border-radius: 50%; background: var(--brand-red); }
  .wordmark__name { font-size: 22px; line-height: 27px; letter-spacing: 1.5px; }
</style>
</head>
<body>
  <section class="card card--front" aria-label="Business card front">
    <div class="holder">
      <p class="holder__name">MARA TAN</p>
      <p class="holder__title">CEO/Founder</p>
    </div>
    <p class="address">42 Cassia Crescent<br>Singapore, SG 390042</p>
    <ul class="contacts">
      <li><svg viewBox="0 0 24 24"><path d="M6.6 10.8a15 15 0 0 0 6.6 6.6l2.2-2.2c.3-.3.7-.4 1-.2 1.1.4 2.3.6 3.6.6.6 0 1 .4 1 1V20c0 .6-.4 1-1 1A17 17 0 0 1 3 4c0-.6.4-1 1-1h3.5c.6 0 1 .4 1 1 0 1.3.2 2.5.6 3.6.1.3 0 .7-.2 1z"/></svg>612 405 3381</li>
      <li><svg viewBox="0 0 24 24"><path d="M7 1h10a2 2 0 0 1 2 2v18a2 2 0 0 1-2 2H7a2 2 0 0 1-2-2V3a2 2 0 0 1 2-2zm0 3v14h10V4zm5 15.5a1 1 0 1 0 0 2 1 1 0 0 0 0-2z"/></svg>847 210 6653</li>
      <li><svg viewBox="0 0 24 24"><path d="M6 2h10l2 2v5H6zM3 10h18a1 1 0 0 1 1 1v7H2v-7a1 1 0 0 1 1-1zm3 9h12v3H6z"/></svg>493 718 2260</li>
      <li><svg viewBox="0 0 24 24"><path d="M2 5h20v14H2zm2 2v.5l8 5.5 8-5.5V7zm0 3v7h16v-7l-8 5.5z"/></svg>hello@lornoprod.com</li>
      <li><svg viewBox="0 0 24 24"><path d="M12 2a10 10 0 1 0 0 20 10 10 0 0 0 0-20zm-1 17.9A8 8 0 0 1 4.2 10L9 15v1a2 2 0 0 0 2 2zm6.9-2.5A2 2 0 0 0 16 16h-1v-3a1 1 0 0 0-1-1H8v-2h2a1 1 0 0 0 1-1V7h2a2 2 0 0 0 2-2v-.4a8 8 0 0 1 2.9 12.8z"/></svg>www.lornoprod.com</li>
    </ul>
    <div class="front-mark">
      <span class="front-mark__dot"></span>
      <span class="front-mark__name">Lorno<br>Productions</span>
    </div>
  </section>

  <section class="card card--back" aria-label="Business card back">
    <div class="wordmark">
      <span class="wordmark__dot"></span>
      <span class="wordmark__name">Lorno<br>Productions</span>
    </div>
  </section>
</body>
</html>
```